Commercial Real Estate Property Sign

Design a 4' x 4' sign that pops. Refer to examples.

Must include the following information:
A space to list (For Sale, For Lease, Build-to-Suite or Available)
BrightKeel,LLC
Commercial Real Estate
company website
My Name (Marcus Pellow)
My Phone #

Industry/Entity Type

Real Estate

```html
<!DOCTYPE html>
<html lang="en">
<head>
<meta charset="utf-8">
<title>BrightKeel LLC – Commercial Real Estate Sign</title>
<link rel="stylesheet" href="https://fonts.googleapis.com/css2?family=Barlow+Semi+Condensed:wght@600;700&family=Barlow:wght@600&family=Open+Sans:wght@400&display=swap">
<style>
  :root {
    --charcoal: #3d3d3d;
    --charcoal-dark: #2e2e2e;
    --black: #000000;
    --orange: #e8650f;
    --ink: #1c1c1c;
    --white: #ffffff;
    --glow: #fbf1df;
    --amber: #e2b77e;
    --bronze: #a9804f;
    --umber: #4a3523;
  }
  * { margin: 0; padding: 0; box-sizing: border-box; }
  html, body { width: 1200px; height: 1200px; overflow: hidden; background: var(--white); }
  .sign { position: relative; width: 1200px; height: 1200px; overflow: hidden; }

  .brand-band {
    position: absolute; left: 0; top: 0; width: 1200px; height: 180px;
    background: linear-gradient(180deg, var(--charcoal) 0%, var(--charcoal-dark) 100%);
  }
  .brand-name {
    position: absolute; left: 0; top: 26px; width: 1200px;
    display: flex; justify-content: center; align-items: center; gap: 40px;
  }
  .brand-mark { width: 28px; height: 90px; background: var(--black); }
  .brand-text {
    font-family: "Open Sans", sans-serif; font-weight: 400; font-size: 78px;
    letter-spacing: 9px; color: var(--white); line-height: 1;
  }
  .brand-rule {
    position: absolute; left: 0; top: 137px; width: 1200px; height: 8px; background: var(--orange);
  }
  .brand-tagline {
    position: absolute; left: 50%; top: 119px; transform: translateX(-50%);
    padding: 0 8px; background: var(--charcoal-dark);
    font-family: "Open Sans", sans-serif; font-size: 34px; color: var(--white); line-height: 1.2;
    white-space: nowrap;
  }

  .web-band {
    position: absolute; left: 0; top: 180px; width: 1200px; height: 60px; background: var(--white);
    display: flex; justify-content: center; align-items: center; gap: 12px;
  }
  .web-icon { width: 24px; height: 24px; }
  .web-address { font-family: "Barlow", sans-serif; font-weight: 600; font-size: 40px; color: var(--orange); }

  .hero-photo {
    position: absolute; left: 0; top: 240px; width: 1200px; height: 960px;
    background:
      radial-gradient(ellipse 48% 30% at 52% 22%, rgba(251,241,223,0.95) 0%, rgba(251,241,223,0) 100%),
      radial-gradient(ellipse 60% 18% at 60% 82%, rgba(255,226,160,0.75) 0%, rgba(255,226,160,0) 100%),
      linear-gradient(90deg, rgba(74,53,35,0.75) 0%, rgba(74,53,35,0.15) 12%, rgba(74,53,35,0) 30%, rgba(74,53,35,0) 75%, rgba(74,53,35,0.2) 90%, rgba(74,53,35,0.7) 100%),
      linear-gradient(180deg, #f4e8d4 0%, #e9d3b0 30%, var(--amber) 52%, var(--bronze) 68%, #d3a764 80%, #8d6a43 92%, var(--umber) 100%);
  }

  .listing-types {
    position: absolute; left: 258px; top: 340px; width: 880px;
    transform: rotate(3deg); transform-origin: left top;
    font-family: "Barlow Semi Condensed", sans-serif; font-weight: 600; color: var(--ink); line-height: 1.15;
  }
  .listing-line { font-size: 74px; white-space: nowrap; }
  .listing-line.first { padding-left: 56px; }
  .initial { color: var(--orange); }
  .divider { font-weight: 400; padding: 0 14px; }

  .contact-band {
    position: absolute; left: 0; top: 1086px; width: 1200px; height: 76px; background: var(--orange);
    display: flex; justify-content: center; align-items: center;
    font-family: "Barlow Semi Condensed", sans-serif; font-weight: 700; font-size: 70px; color: var(--ink);
    letter-spacing: 1px; white-space: nowrap;
  }
  .contact-name { margin-right: 22px; }
</style>
</head>
<body>
<main class="sign">
  <header class="brand-band">
    <div class="brand-name">
      <span class="brand-mark"></span>
      <span class="brand-text">BrightKeel LLC</span>
    </div>
    <div class="brand-rule"></div>
    <div class="brand-tagline">Commercial Real Estate</div>
  </header>

  <div class="web-band">
    <svg class="web-icon" viewBox="0 0 24 24" fill="none" stroke="#e8650f" stroke-width="2">
      <circle cx="12" cy="12" r="10"/>
      <ellipse cx="12" cy="12" rx="4.5" ry="10"/>
      <line x1="2" y1="12" x2="22" y2="12"/>
      <line x1="4" y1="6.5" x2="20" y2="6.5"/>
      <line x1="4" y1="17.5" x2="20" y2="17.5"/>
    </svg>
    <span class="web-address">www.mybrightkeel.com</span>
  </div>

  <div class="hero-photo" role="img" aria-label="Businessman on the phone standing in an empty office with floor-to-ceiling windows overlooking a city skyline at sunset, warm light across the floor"></div>

  <div class="listing-types">
    <div class="listing-line first"><span class="initial">F</span>or Sale<span class="divider">|</span><span class="initial">F</span>or Lease</div>
    <div class="listing-line"><span class="initial">B</span>uild-to-Suite or Available</div>
  </div>

  <footer class="contact-band">
    <span class="contact-name">MARCUS PELLOW</span>
    <span class="contact-phone">469.555.0182</span>
  </footer>
</main>
</body>
</html>
```